Roofing company in Toronto, Canada needs a logo design and business card design

We need a business card and logo created for our company. Our company is "KLV Roofing" which provides roofing services for commercial and residential customers. We serve customers in the Greater Toronto Area (in Canada) thus the name KLV.

We want the logo and business card to be a modern design displaying professionalism and quality in the work. We would prefer rounded corners for the business cards but are open to other ideas. The cards should be pleasant and appealing to customers.

Target Market(s)

Commercial and Residential customers

Industry/Entity Type

Roofing

Contact Information for Business Card

Logo Text

KLV Roofing

Requirements
Nice to have
• Colours that are pleasing to the eye but at the same time should stand out from other business cards. If the design can incorporate the name of KLV Roofing and the actual concept of roofing that would be nice.
Should not have
• Do not want the business cards or logo to be childish looking. Need to look professionally designed.

```html
<!DOCTYPE html>
<html lang="en">
<head>
<meta charset="UTF-8">
<title>KLV Roofing – Business Card</title>
<link rel="stylesheet" href="https://fonts.googleapis.com/css2?family=Lato:wght@400;700&display=swap">
<style>
  :root {
    --bg: #e7e5e1;
    --card-white: #fbfbfa;
    --card-dark: #55575a;
    --ink: #5b5d60;
    --ink-soft: #6f7174;
    --accent: #f0a81c;
    --accent-deep: #e39a12;
    --rule: #c9c9c9;
    --white: #ffffff;
  }
  * { box-sizing: border-box; margin: 0; padding: 0; }
  html, body { width: 1200px; height: 780px; overflow: hidden; }
  body {
    background: var(--bg);
    font-family: "Lato", Arial, sans-serif;
    display: flex;
    align-items: center;
    justify-content: center;
    gap: 40px;
  }
  .card {
    position: relative;
    width: 540px;
    height: 309px;
    border-radius: 14px;
    overflow: hidden;
    box-shadow: 0 6px 18px rgba(0,0,0,0.18);
  }

  /* Front */
  .card--front { background: var(--card-white); }
  .front__main {
    position: absolute; inset: 0 0 52px 0;
    display: flex; align-items: center;
  }
  .brand {
    width: 50%;
    display: flex; align-items: center; justify-content: center; gap: 10px;
  }
  .brand__mark {
    width: 18px; height: 18px; background: var(--accent);
  }
  .brand__name {
    font-weight: 700; font-size: 34px; color: var(--ink); letter-spacing: 0.5px;
  }
  .divider {
    width: 1px; height: 120px; background: var(--rule);
  }
  .contact {
    width: 50%; padding-left: 40px;
  }
  .contact__name {
    font-weight: 700; font-size: 20px; color: var(--ink); letter-spacing: 0.5px; text-transform: uppercase;
  }
  .contact__title {
    font-size: 14px; color: var(--accent); margin-bottom: 22px;
  }
  .contact__list { list-style: none; }
  .contact__item {
    display: flex; align-items: center; gap: 9px;
    font-size: 13px; color: var(--ink-soft); line-height: 22px;
  }
  .contact__icon {
    width: 15px; height: 15px; background: var(--accent); border-radius: 2px;
    display: flex; align-items: center; justify-content: center;
  }
  .front__band {
    position: absolute; left: 0; right: 0; bottom: 0; height: 52px;
    background: linear-gradient(90deg, var(--accent), var(--accent-deep));
    display: flex; align-items: center; justify-content: center;
    color: var(--white); font-size: 14px; letter-spacing: 0.3px;
  }

  /* Back */
  .card--back {
    background: var(--card-dark);
    display: flex; align-items: center; justify-content: center;
  }
  .card--back .brand { width: auto; }
  .card--back .brand__name { color: var(--white); font-size: 40px; }
  .card--back .brand__mark { width: 20px; height: 20px; }
</style>
</head>
<body>
  <section class="card card--front">
    <div class="front__main">
      <div class="brand">
        <span class="brand__mark"></span>
        <span class="brand__name">KLV Roofing</span>
      </div>
      <div class="divider"></div>
      <div class="contact">
        <p class="contact__name">Marcus Hale</p>
        <p class="contact__title">Managing Director</p>
        <ul class="contact__list">
          <li class="contact__item">
            <span class="contact__icon"><svg width="9" height="9" viewBox="0 0 10 10"><path d="M2 1l2 2-1 1.2c.6 1.3 1.5 2.2 2.8 2.8L7 6l2 2-1.3 1.5C4.5 9 1 5.5.5 2.3z" fill="#fff"/></svg></span>
            (01) 4827 5310
          </li>
          <li class="contact__item">
            <span class="contact__icon"><svg width="9" height="9" viewBox="0 0 10 10"><rect x="2.5" y="0.5" width="5" height="9" rx="1" fill="none" stroke="#fff"/><circle cx="5" cy="7.8" r="0.6" fill="#fff"/></svg></span>
            (01) 4827 5310
          </li>
          <li class="contact__item">
            <span class="contact__icon"><svg width="9" height="9" viewBox="0 0 10 10"><rect x="0.5" y="2" width="9" height="6" fill="none" stroke="#fff"/><path d="M.5 2L5 5.5 9.5 2" fill="none" stroke="#fff"/></svg></span>
            info@klvroofing.com
          </li>
          <li class="contact__item">
            <span class="contact__icon"><svg width="9" height="9" viewBox="0 0 10 10"><circle cx="5" cy="5" r="4.3" fill="none" stroke="#fff"/><ellipse cx="5" cy="5" rx="1.8" ry="4.3" fill="none" stroke="#fff"/><path d="M.7 5h8.6" stroke="#fff"/></svg></span>
            www.klvroofing.com
          </li>
        </ul>
      </div>
    </div>
    <div class="front__band">PO BOX 418 Harbour Lane, 5th Street Toronto, CANADA</div>
  </section>

  <section class="card card--back">
    <div class="brand">
      <span class="brand__mark"></span>
      <span class="brand__name">KLV Roofing</span>
    </div>
  </section>
</body>
</html>
```